Stationery Design Project

I need a stationary design for our company. we are based in Houston, TX and we are called Mira Vell Lending. And we are wanting to brand our MoneyMendPlus program, which includes our tax preparation and restoration, credit repair service. Although our business offers other programs, we are interested in mainly focusing on The MoneyMendPlus program. We are looking for way to brand our ourselves and I believe that a great stationery design will help in achieving this goal. Our logo design is blue and light blue. the slogan is orange.

Industry/Entity Type

Business

Requirements
Must have
• Address: 30871 Calloway Ln. B-22
Houston, TX 75419
Tel. 555-318-6207
Fax 555-294-7153
www.miravelllending.example
info@miravelllending.example
Our Slogan: Confidence, Renewed!

```html
<!DOCTYPE html>
<html lang="en">
<head>
<meta charset="utf-8">
<title>MoneyMendPlus – Business Card</title>
<link href="https://fonts.googleapis.com/css2?family=Arimo:wght@400;700&family=Tinos:wght@400;700&display=swap" rel="stylesheet">
<style>
  :root {
    --backdrop: #e9e6e1;
    --card: #ffffff;
    --navy: #173f66;
    --blue: #1f79b8;
    --sky: #2aa0d8;
    --orange: #f29a1f;
    --ink: #2b2b2b;
    --rule: #c9c9c9;
    --url-light: #3a4f66;
  }
  * { margin: 0; padding: 0; box-sizing: border-box; }
  html, body { width: 1200px; height: 371px; overflow: hidden; background: var(--backdrop); }
  .canvas { position: relative; width: 1200px; height: 371px; }

  .card {
    position: absolute; top: 28px; width: 550px; height: 312px;
    background: var(--card); overflow: hidden;
    box-shadow: 0 1px 3px rgba(0,0,0,.25);
  }
  .card--front { left: 30px; }
  .card--back { left: 620px; }

  /* Front */
  .brand { position: absolute; left: 10px; width: 300px; top: 84px; text-align: center; }
  .brand__mark {
    display: block; width: 44px; height: 44px; margin: 0 auto 26px;
    background: var(--blue);
  }
  .brand__name {
    font-family: "Arimo", sans-serif; font-weight: 400;
    font-size: 34px; line-height: 38px; color: var(--blue); letter-spacing: -.5px;
  }
  .brand__slogan {
    margin-top: 4px; font-family: "Arimo", sans-serif; font-weight: 700;
    font-size: 18px; color: var(--orange); letter-spacing: 1.5px;
  }
  .divider { position: absolute; left: 318px; top: 62px; width: 1px; height: 148px; background: var(--rule); }

  .contact { position: absolute; left: 340px; top: 64px; font-family: "Tinos", serif; font-size: 14px; color: var(--ink); line-height: 21px; }
  .contact__address { margin-bottom: 12px; }
  .contact__row { display: flex; align-items: center; height: 22px; white-space: nowrap; }
  .contact__row svg { width: 12px; height: 12px; margin-right: 7px; fill: var(--ink); flex: none; }

  .swoosh { position: absolute; left: 0; bottom: 0; width: 550px; height: 64px; }

  /* Back */
  .identity { position: absolute; left: 0; right: 0; top: 110px; text-align: center; }
  .identity__mark { display: block; width: 40px; height: 40px; margin: 0 auto 40px; background: var(--navy); }
  .identity__name { font-family: "Tinos", serif; font-size: 18px; color: var(--navy); }
  .web {
    position: absolute; left: 0; right: 0; top: 276px; text-align: center;
    font-family: "Tinos", serif; font-size: 15px; letter-spacing: 2.6px; color: var(--url-light);
  }
  .web strong { color: var(--navy); font-weight: 700; }
</style>
</head>
<body>
<div class="canvas">

  <section class="card card--front">
    <div class="brand">
      <span class="brand__mark"></span>
      <div class="brand__name">MoneyMendPlus</div>
      <div class="brand__slogan">Confidence, Renewed!</div>
    </div>

    <div class="divider"></div>

    <div class="contact">
      <div class="contact__address">30871 Calloway Ln. B-22<br>Houston, TX 75419</div>
      <div class="contact__row">
        <svg viewBox="0 0 12 12" aria-label="Phone"><circle cx="6" cy="6" r="6"/><path d="M3.6 3.2c.4-.4.9-.3 1.1.1l.5 1c.1.3 0 .5-.2.7l-.3.3c.4.8 1 1.4 1.8 1.8l.3-.3c.2-.2.5-.3.7-.2l1 .5c.4.2.5.7.1 1.1-.6.6-1.5.7-2.3.3C5 7.8 4.2 7 3.5 5.7c-.4-.9-.4-1.8.1-2.5z" fill="#fff"/></svg>
        555-318-6207
      </div>
      <div class="contact__row">
        <svg viewBox="0 0 12 12" aria-label="Fax"><rect x="3" y="1" width="6" height="4"/><rect x="0" y="5" width="12" height="5" rx="1"/><rect x="3" y="8" width="6" height="3" fill="#fff"/></svg>
        555-294-7153
      </div>
      <div class="contact__row">
        <svg viewBox="0 0 12 12" aria-label="Email"><circle cx="6" cy="6" r="6"/><path d="M2.8 4h6.4v4.2H2.8z" fill="#fff"/><path d="M2.8 4L6 6.4 9.2 4" stroke="#2b2b2b" stroke-width=".8" fill="none"/></svg>
        info@miravelllending.example
      </div>
      <div class="contact__row">
        <svg viewBox="0 0 12 12" aria-label="Website"><circle cx="6" cy="6" r="5.3" fill="none" stroke="#2b2b2b" stroke-width="1.2"/><ellipse cx="6" cy="6" rx="2.2" ry="5.3" fill="none" stroke="#2b2b2b" stroke-width="1"/><path d="M.8 6h10.4" stroke="#2b2b2b" stroke-width="1"/></svg>
        www.miravelllending.example
      </div>
    </div>

    <svg class="swoosh" viewBox="0 0 550 64" preserveAspectRatio="none" aria-hidden="true">
      <defs>
        <linearGradient id="swoosh-blue" x1="0" x2="1" y1="0" y2="0">
          <stop offset="0" stop-color="#173f66"/>
          <stop offset=".45" stop-color="#2aa0d8"/>
          <stop offset="1" stop-color="#173f66"/>
        </linearGradient>
      </defs>
      <path d="M0 28 C120 6 220 30 330 22 C430 14 500 6 550 0 L550 12 C480 20 420 30 320 38 C200 48 120 30 0 46Z" fill="#f29a1f"/>
      <path d="M0 48 C120 34 210 52 330 42 C430 34 500 22 550 14 L550 64 L0 64Z" fill="url(#swoosh-blue)"/>
    </svg>
  </section>

  <section class="card card--back">
    <div class="identity">
      <span class="identity__mark"></span>
      <div class="identity__name">Mira Vell Lending</div>
    </div>
    <div class="web">www.<strong>miravelllending</strong>.example</div>
  </section>

</div>
</body>
</html>
```